Business Card Design Project

Business Card
We are rebranding with a new logo
Industry/Entity Type
Business
Contact Information for Business Card
Dennis Morvale +61 487215963 dennis@quorv.com.au P.O. Box 872 Fernlow QLD 4309
Requirements
Must have
- Logo

```html
<!DOCTYPE html>
<html lang="en">
<head>
<meta charset="utf-8">
<title>Quorv International – Business Card</title>
<link rel="stylesheet" href="https://fonts.googleapis.com/css2?family=Roboto:wght@400;500&family=Roboto+Condensed:wght@700&display=swap">
<style>
  :root {
    --backdrop: #1c1c1c;
    --card: #f4f4f4;
    --brand-blue: #1a86c0;
    --accent-orange: #ee7a1c;
    --text-grey: #555555;
    --rule-grey: #9a9a9a;
  }
  * { margin: 0; padding: 0; box-sizing: border-box; }
  html, body {
    width: 1200px;
    height: 960px;
    overflow: hidden;
    background: var(--backdrop);
  }
  .stage {
    position: relative;
    width: 1200px;
    height: 960px;
  }
  .business-card {
    position: absolute;
    left: 223px;
    top: 265px;
    width: 754px;
    height: 430px;
    background: var(--card);
  }
  .brand {
    position: absolute;
    right: 57px;
    top: 168px;
    display: flex;
    align-items: center;
    gap: 12px;
  }
  .brand-dot {
    width: 18px;
    height: 18px;
    border-radius: 50%;
    background: var(--accent-orange);
  }
  .brand-name {
    font-family: 'Roboto', sans-serif;
    font-weight: 500;
    font-size: 30px;
    letter-spacing: 1px;
    color: var(--brand-blue);
  }
  .holder-name {
    position: absolute;
    left: 51px;
    top: 264px;
    font-family: 'Roboto Condensed', sans-serif;
    font-weight: 700;
    font-size: 27px;
    color: var(--brand-blue);
    text-transform: uppercase;
  }
  .contact-list {
    position: absolute;
    left: 51px;
    top: 317px;
    list-style: none;
    font-family: 'Roboto', sans-serif;
    font-size: 18px;
    color: var(--text-grey);
  }
  .contact-item {
    display: flex;
    align-items: center;
    height: 23.5px;
  }
  .contact-icon {
    width: 18px;
    height: 18px;
    margin-right: 11px;
    fill: var(--brand-blue);
  }
  .divider {
    position: absolute;
    left: 276px;
    top: 344px;
    width: 1px;
    height: 44px;
    background: var(--rule-grey);
  }
  .postal-address {
    position: absolute;
    left: 310px;
    top: 342px;
    font-family: 'Roboto', sans-serif;
    font-style: normal;
    font-size: 18px;
    line-height: 23px;
    color: var(--text-grey);
  }
</style>
</head>
<body>
<main class="stage">
  <section class="business-card">
    <div class="brand">
      <span class="brand-dot"></span>
      <span class="brand-name">Quorv International</span>
    </div>

    <h1 class="holder-name">Dennis Morvale</h1>

    <ul class="contact-list">
      <li class="contact-item">
        <svg class="contact-icon" viewBox="0 0 24 24" aria-hidden="true"><path d="M6.6 10.8a15.1 15.1 0 0 0 6.6 6.6l2.2-2.2a1 1 0 0 1 1-.25 11.4 11.4 0 0 0 3.6.57 1 1 0 0 1 1 1V20a1 1 0 0 1-1 1A17 17 0 0 1 3 4a1 1 0 0 1 1-1h3.5a1 1 0 0 1 1 1c0 1.25.2 2.45.57 3.57a1 1 0 0 1-.25 1z"/></svg>
        +61 487215963
      </li>
      <li class="contact-item">
        <svg class="contact-icon" viewBox="0 0 24 24" aria-hidden="true"><path d="M2 5h20v14H2z M3.5 6.5v.6l8.5 5.6 8.5-5.6v-.6z" fill-rule="evenodd"/></svg>
        dennis@quorv.com.au
      </li>
      <li class="contact-item">
        <svg class="contact-icon" viewBox="0 0 24 24" aria-hidden="true"><circle cx="12" cy="12" r="10"/><path d="M8 6c2 1 1 3 3 3s1 3-1 3-3 2-2 4M15 15c1-1 3-1 4 0" stroke="#f4f4f4" stroke-width="1.6" fill="none"/></svg>
        www.quorv.com.au
      </li>
    </ul>

    <span class="divider"></span>

    <address class="postal-address">
      P.O. Box 872<br>
      Fernlow QLD 4309
    </address>
  </section>
</main>
</body>
</html>
```